Modern card design needed for building development company

We are looking for a sharp modern new look for our business cards.
We are a New Zealand based company called TKR Ventures NZ LTD that specialises in subdividing large sections, housing and commercial buildings.
We have attached a photo of the current logo and would like to see it improved somehow as it looks a bit dated.
We are open to any colours.

Target Market(s)

Investors, Property buyers

Industry/Entity Type

Investment

Contact Information for Business Card

TKR VENTURES NZ LTD
www.tkrventuresnz.co.nz

Damon Whitcombe
Phone +64 21 938 104
Email dpwhitcombe@korumail.co.nz

Font styles to use
Serif
Sans Serif

Colors
0792cd
33a6d7
85cae6
6b449b
886aae
f04a50
ec1f27
f37122
f68d4d

Requirements
Must have
• Please try and make the logo more modern or if you have a similar one we would like to see it.

```html
<!DOCTYPE html>
<html lang="en">
<head>
<meta charset="utf-8">
<title>TKR Ventures NZ LTD — Business Card</title>
<link href="https://fonts.googleapis.com/css2?family=Oswald:wght@500&family=Work+Sans:wght@300;400;500&display=swap" rel="stylesheet">
<style>
  :root {
    --backdrop: #232324;
    --card: #161617;
    --card-edge: #202021;
    --silver: #c9c9c9;
    --silver-soft: #9a9a9a;
    --muted: #5b5b5b;
    --rule: #8a8a8a;
  }
  * { margin: 0; padding: 0; box-sizing: border-box; }
  html, body {
    width: 1200px; height: 900px; overflow: hidden;
    background: var(--backdrop);
  }
  .stage {
    position: relative; width: 1200px; height: 900px;
    display: flex; flex-direction: column; align-items: center; justify-content: center;
    gap: 44px;
  }
  .card {
    width: 640px; height: 366px;
    background: linear-gradient(160deg, var(--card-edge) 0%, var(--card) 70%);
    box-shadow: 0 10px 30px rgba(0,0,0,.45);
    position: relative;
  }
  /* front */
  .card-front {
    display: flex; flex-direction: column; align-items: center; justify-content: center;
  }
  .brand {
    display: flex; align-items: center; gap: 12px;
    margin-top: 30px;
  }
  .brand-mark {
    width: 14px; height: 14px; background: var(--silver);
  }
  .brand-name {
    font-family: 'Work Sans', sans-serif; font-weight: 500;
    font-size: 20px; letter-spacing: 2.5px; color: var(--silver);
  }
  .address {
    margin-top: 22px;
    font-family: 'Work Sans', sans-serif; font-weight: 400;
    font-size: 13.5px; letter-spacing: .4px; color: var(--muted);
  }
  /* back */
  .card-back {
    display: flex; align-items: center;
  }
  .identity {
    width: 262px; text-align: right; margin-left: 0;
  }
  .person-name {
    font-family: 'Oswald', sans-serif; font-weight: 500;
    font-size: 28px; letter-spacing: .5px; line-height: 1;
    color: var(--silver-soft);
    text-transform: uppercase;
  }
  .person-role {
    margin-top: 4px;
    font-family: 'Work Sans', sans-serif; font-weight: 400;
    font-size: 13px; letter-spacing: 1px; color: var(--muted);
    text-transform: uppercase;
  }
  .divider {
    width: 1.5px; height: 66px; background: var(--rule);
    margin: 0 22px 0 30px;
  }
  .contacts { list-style: none; }
  .contact {
    display: flex; align-items: center; gap: 14px;
    font-family: 'Work Sans', sans-serif; font-weight: 300;
    font-size: 16px; letter-spacing: .6px; color: var(--silver);
    line-height: 21px;
  }
  .contact svg { width: 11px; height: 11px; flex: none; }
</style>
</head>
<body>
<main class="stage">
  <section class="card card-front">
    <div class="brand">
      <span class="brand-mark"></span>
      <span class="brand-name">TKR VENTURES NZ LTD</span>
    </div>
    <p class="address">PO BOX 48215 Hillcrest Auckland New Zealand</p>
  </section>

  <section class="card card-back">
    <div class="identity">
      <h1 class="person-name">Damon Whitcombe</h1>
      <p class="person-role">Director</p>
    </div>
    <span class="divider"></span>
    <ul class="contacts">
      <li class="contact">
        <svg viewBox="0 0 12 12" aria-hidden="true"><path d="M2.5 1h2l1 2.5-1.3 1A7 7 0 0 0 7.5 7.8l1-1.3L11 7.5v2A1.5 1.5 0 0 1 9.5 11 8.5 8.5 0 0 1 1 2.5 1.5 1.5 0 0 1 2.5 1z" fill="var(--silver-soft)"/></svg>
        +64 21 938 104
      </li>
      <li class="contact">
        <svg viewBox="0 0 12 12" aria-hidden="true"><rect x="1" y="2.5" width="10" height="7" fill="none" stroke="var(--silver-soft)" stroke-width="1.2"/><path d="M1 2.8 6 6.6l5-3.8" fill="none" stroke="var(--silver-soft)" stroke-width="1.2"/></svg>
        dpwhitcombe@korumail.co.nz
      </li>
      <li class="contact">
        <svg viewBox="0 0 12 12" aria-hidden="true"><circle cx="6" cy="6" r="5" fill="none" stroke="var(--silver-soft)" stroke-width="1.1"/><ellipse cx="6" cy="6" rx="2.2" ry="5" fill="none" stroke="var(--silver-soft)" stroke-width="1"/><path d="M1 6h10" stroke="var(--silver-soft)" stroke-width="1"/></svg>
        www.tkrventuresnz.co.nz
      </li>
    </ul>
  </section>
</main>
</body>
</html>
```